Logo, Web and Mobile Designs for enterprise social media platform

All the details are in the attached document, please start reading the scope document first which explains what is this project about and the details about the needed deliverables, after that please read the UI_Requirements document which will detail what is expected regarding the coded web version since this is a coded contest, it is very important that you meet the UI requirements or suggest something else but we will need to agree first before working on the coded version

Good Luck

Target Market(s)

Enterprise Social Media

Industry/Entity Type

Media

Coding

Coded - Design and coding required

Number of Pages Required

5+ page

Font styles to use
Sans Serif

Requirements
Must have
• All the must haves are listed in the scope document so please check before you start

```html
<!DOCTYPE html>
<html lang="en">
<head>
<meta charset="utf-8">
<title>Teamora – Organizer Details</title>
<link href="https://fonts.googleapis.com/css2?family=Roboto:wght@300;400;500&display=swap" rel="stylesheet">
<style>
:root{
  --blue:#1e8bc3;
  --blue-btn:#0d87c8;
  --footer:#1f8ab6;
  --text:#555b63;
  --muted:#666;
  --line:#e3e3e3;
  --page:#ececec;
  --side:#f3f3f3;
  --orange:#f6a11a;
  --red:#e0161b;
}
*{box-sizing:border-box;margin:0;padding:0}
html,body{width:1200px;height:912px;overflow:hidden}
body{font-family:'Roboto',sans-serif;background:var(--page);color:var(--text);position:relative}
.abs{position:absolute}

/* header */
.topbar{position:absolute;left:0;top:0;width:1200px;height:70px;background:#fafafa;border-bottom:1px solid #dcdcdc}
.topbar .sep{position:absolute;top:0;width:1px;height:70px;background:#e6e6e6}
.brand{position:absolute;left:168px;top:16px;display:flex;align-items:center;gap:8px}
.brand-dot{width:38px;height:38px;border-radius:50%;background:var(--orange)}
.brand-name{font-size:30px;font-weight:400;color:var(--blue);letter-spacing:.3px}
.avatar{position:absolute;left:746px;top:20px;width:34px;height:34px;border-radius:50%;background:linear-gradient(135deg,#6b5a50,#2d2826)}
.user{position:absolute;left:793px;top:26px;font-size:17px;color:#555}
.badge{position:absolute;width:22px;height:16px;border-radius:8px;color:#fff;font-size:11px;text-align:center;line-height:16px}

/* frame */
.frame{position:absolute;left:99px;top:105px;width:1001px;height:623px;background:#fff;border:1px solid #dcdcdc}
.sidebar{position:absolute;left:0;top:0;width:278px;height:621px;background:var(--side);border-right:1px solid #e2e2e2}
.side-main{position:absolute;left:0;width:278px;height:52px;border-bottom:1px solid var(--line);font-size:15.5px;color:#444;display:flex;align-items:center;padding-left:46px}
.side-main svg{position:absolute;left:18px}
.side-list{position:absolute;left:0;top:231px;width:278px;list-style:none}
.side-list li{height:32.6px;border-bottom:1px solid var(--line);display:flex;align-items:center;padding-left:41px;font-size:16px;font-weight:300;color:#444;position:relative}
.side-list li::before{content:"";position:absolute;left:19px;top:13px;width:5px;height:5px;border-right:1.3px solid #555;border-top:1.3px solid #555;transform:rotate(45deg)}
.side-list li.active{color:var(--blue);font-weight:500}

.card{position:absolute;left:311px;top:41px;width:660px;height:537px;border:1px solid #e6e6e6;background:#fff}
.card-head{height:49px;background:#f6f7f8;border-bottom:1px solid #e2e2e2;display:flex;align-items:center;padding-left:22px;gap:10px;font-size:16px;color:#555}

.label{position:absolute;left:432px;font-size:15px;color:#666}
.field{position:absolute;height:38px;border:1px solid #e2e2e2;background:#fff;font-size:11px;color:#444;display:flex;align-items:center;padding-left:16px}
.field.sel::after{content:"";position:absolute;right:16px;top:14px;width:5px;height:5px;border-right:1.2px solid #555;border-bottom:1.2px solid #555;transform:rotate(45deg)}
.plus{position:absolute;width:43px;height:38px;background:var(--blue-btn);display:flex;align-items:center;justify-content:center}
.btn-add{position:absolute;left:595px;top:618px;width:161px;height:36px;background:var(--blue-btn);color:#fff;font-size:16px;font-weight:500;display:flex;align-items:center;justify-content:center;border-radius:2px;box-shadow:0 2px 0 #0a6a9c}

/* footer */
.footer{position:absolute;left:0;top:765px;width:1200px;height:147px;background:var(--footer);color:#fff;text-align:center}
.social{position:absolute;left:513px;top:28px;display:flex;gap:12px}
.social span{width:24px;height:24px;border-radius:4px;background:#fff}
.flinks{position:absolute;top:70px;width:1200px;font-size:14.5px;font-weight:300}
.flinks span{margin:0 6px}
.copy{position:absolute;top:100px;width:1200px;font-size:14.5px;font-weight:300}
</style>
</head>
<body>

<header class="topbar">
  <svg class="abs" style="left:101px;top:29px" width="18" height="15" viewBox="0 0 18 15"><rect width="18" height="3" fill="#777"/><rect y="6" width="18" height="3" fill="#777"/><rect y="12" width="18" height="3" fill="#777"/></svg>
  <div class="sep" style="left:144px"></div>
  <div class="brand"><span class="brand-dot"></span><span class="brand-name">Teamora</span></div>
  <div class="avatar" role="img" aria-label="User profile photo"></div>
  <div class="user">Alex Carter</div>
  <svg class="abs" style="left:887px;top:33px" width="12" height="7" viewBox="0 0 12 7"><path d="M0 0h12L6 7z" fill="#555"/></svg>
  <div class="sep" style="left:922px"></div>
  <svg class="abs" style="left:945px;top:26px" width="20" height="19" viewBox="0 0 20 19"><rect width="20" height="5" fill="#666"/><rect y="7" width="20" height="5" fill="#666"/><rect y="14" width="20" height="5" fill="#666"/></svg>
  <div class="badge" style="left:956px;top:16px;background:var(--orange)">8</div>
  <div class="sep" style="left:991px"></div>
  <svg class="abs" style="left:1011px;top:26px" width="20" height="20" viewBox="0 0 20 20"><circle cx="8" cy="8" r="6" fill="none" stroke="#666" stroke-width="3"/><path d="M12.5 12.5L18 18" stroke="#666" stroke-width="3.5" stroke-linecap="round"/></svg>
  <div class="sep" style="left:1051px"></div>
  <svg class="abs" style="left:1072px;top:26px" width="18" height="20" viewBox="0 0 18 20"><path d="M9 1c-4 0-6 3-6 6v5l-2 3h16l-2-3V7c0-3-2-6-6-6z" fill="#666"/><circle cx="9" cy="17.5" r="2.3" fill="#666"/></svg>
  <div class="badge" style="left:1078px;top:16px;background:var(--blue)">8</div>
</header>

<main class="frame">
  <nav class="sidebar">
    <div class="side-main" style="top:6px">
      <svg width="14" height="13" viewBox="0 0 14 13"><rect width="6" height="5.5" fill="var(--blue)"/><rect x="8" width="6" height="5.5" fill="var(--blue)"/><rect y="7.5" width="6" height="5.5" fill="var(--blue)"/><rect x="8" y="7.5" width="6" height="5.5" fill="var(--blue)"/></svg>
      VIEW DASHBOARD
    </div>
    <div class="side-main" style="top:58px">
      <svg width="14" height="14" viewBox="0 0 14 14"><rect y="2" width="14" height="12" fill="none" stroke="var(--blue)" stroke-width="1.6"/><rect y="2" width="14" height="3" fill="var(--blue)"/><rect x="3" width="2" height="3" fill="var(--blue)"/><rect x="9" width="2" height="3" fill="var(--blue)"/><path d="M3 8h8M3 11h8M5.5 6v7M8.5 6v7" stroke="var(--blue)" stroke-width="1"/></svg>
      VIEW EVENT
    </div>
    <ul class="side-list">
      <li>About Us</li><li>Speakers</li><li>Track</li><li>Sessions</li><li>Tickets</li>
      <li class="active">ORGANIZERS</li><li>Sponsors</li><li>Exhibitor</li><li>Security</li><li>Members</li>
    </ul>
  </nav>
  <section class="card">
    <div class="card-head">
      <svg width="18" height="16" viewBox="0 0 18 16"><path d="M17 1L1 7l6 2 1 6 3-4 4 3z M7 9l10-8" fill="none" stroke="#555" stroke-width="1.5" stroke-linejoin="round"/></svg>
      ORGANIZER DETAILS
    </div>
  </section>
</main>

<div class="label" style="top:241px">Organizer Name :</div>
<div class="field" style="left:596px;top:231px;width:451px;color:var(--red)">This is a required field</div>

<div class="label" style="top:292px">Photo :</div>
<div class="field" style="left:596px;top:282px;width:197px">Enter Phone</div>
<div class="plus" style="left:803px;top:282px"><svg width="12" height="12" viewBox="0 0 12 12"><path d="M6 0v12M0 6h12" stroke="#fff" stroke-width="3"/></svg></div>

<div class="label" style="top:347px">Upload Organizer Photo :</div>
<svg class="abs" style="left:604px;top:349px" width="18" height="13" viewBox="0 0 18 13"><path d="M4 13a4 4 0 010-8 5 5 0 019.5-1A4.5 4.5 0 0114 13z" fill="var(--blue)"/><path d="M9 11V6M6.5 8L9 5.5 11.5 8" stroke="#fff" stroke-width="1.6" fill="none"/></svg>

<div class="label" style="top:395px">Organizer Description :</div>
<div class="field" style="left:596px;top:385px;width:451px;height:88px"></div>

<div class="label" style="top:501px">Organizer Social Links :</div>
<div class="field sel" style="left:596px;top:491px;width:197px">Select Link Type</div>
<div class="field sel" style="left:802px;top:491px;width:189px">http://example</div>
<div class="plus" style="left:1002px;top:491px"><svg width="12" height="12" viewBox="0 0 12 12"><path d="M6 0v12M0 6h12" stroke="#fff" stroke-width="3"/></svg></div>

<div class="label" style="top:561px;font-size:14px">Organizer External Links :</div>
<div class="field sel" style="left:596px;top:551px;width:197px">Enter link Title</div>
<div class="field sel" style="left:802px;top:551px;width:189px">http://example</div>
<div class="plus" style="left:1002px;top:551px"><svg width="12" height="12" viewBox="0 0 12 12"><path d="M6 0v12M0 6h12" stroke="#fff" stroke-width="3"/></svg></div>

<div class="btn-add">ADD ORGANIZER</div>

<footer class="footer">
  <div class="social"><span></span><span></span><span></span><span></span><span></span></div>
  <div class="flinks">Home<span>/</span>Contact<span>/</span>Topics<span>/</span>Posts and Comments<span>/</span>Discussion<span>/</span>Videos Links</div>
  <div class="copy">Copyright @ 2015 - 2015.Teamora. All Rights Reserved.</div>
</footer>

</body>
</html>
```